Business Card Design for a new Senior Concierge Business 1.3.24

I need a professional business card to handout at networking events for my senior helper business. I would like to use the logo I have uploaded. The design should be clear and easy to read and should list the following information...
Delia Parkhurst
Owner
www.HarborlightElderAides.com
Willowmere, Texas
936.482.5079
Delia@harborlightelderaides.com

Target Market(s)

Senior Citizens

Industry/Entity Type

Personal Helper/ Assisstant

Contact Information for Business Card

I have included the details in the project description box.

Font styles to use
Serif

Colors
0054AA
0677BA
7BADD7
CADEEF
E8F1F8
59FF00
82FF00
B8FF75
E3FFCB
F4FFEA
E54698
E96AAD
F1A4CE
F9D9EA
FCEFF6
6B429C
8869AF
B7A5CE
E3DAEB
F3F0F8

Requirements
Must have
• Include uploaded logo
Nice to have
• The log that has been uploaded
Should not have
• No crazy fonts

```html
<!DOCTYPE html>
<html lang="en">
<head>
<meta charset="utf-8">
<title>Harborlight Elder Aides – Business Card</title>
<link href="https://fonts.googleapis.com/css2?family=Oswald:wght@700&family=Lato:wght@400&display=swap" rel="stylesheet">
<style>
  :root{
    --stage:#3b3b3b;
    --card:#ffffff;
    --purple:#6a2ee8;
    --pink:#d81b5c;
    --teal:#0a8f94;
    --ink:#1c1c1c;
    --rule:#c9c2e8;
  }
  *{margin:0;padding:0;box-sizing:border-box}
  html,body{width:1047px;height:1200px;overflow:hidden;background:var(--stage)}
  .canvas{position:relative;width:1047px;height:1200px}
  .card{position:absolute;left:156px;width:743px;height:425px;background:var(--card);border-radius:19px;overflow:hidden}
  .card--front{top:120px}
  .card--back{top:634px}

  .brand-tag{position:absolute;top:40px;right:34px;display:flex;align-items:center;gap:8px;
    font-family:"Lato",sans-serif;font-size:14px;color:var(--purple)}
  .brand-dot{width:14px;height:14px;border-radius:50%;background:var(--pink)}

  .identity{position:absolute;right:414px;top:186px;text-align:right}
  .identity__name{font-family:"Oswald",sans-serif;font-weight:700;font-size:37px;line-height:44px;
    color:var(--purple);letter-spacing:0;text-transform:uppercase;white-space:nowrap}
  .identity__role{font-family:"Lato",sans-serif;font-size:19px;line-height:20px;color:var(--pink);margin-top:-4px}

  .divider{position:absolute;left:352px;top:179px;width:1px;height:68px;background:var(--rule)}

  .contacts{position:absolute;left:378px;top:175px;list-style:none;font-family:"Lato",sans-serif;color:var(--ink)}
  .contacts li{display:flex;align-items:center;gap:10px;height:25.5px;font-size:18px}
  .contacts li.contacts__phone{font-size:20px}
  .contacts svg{width:17px;height:17px;flex:none}

  .location{position:absolute;left:273px;top:354px;display:flex;align-items:center;gap:8px;
    font-family:"Lato",sans-serif;font-size:20px;color:var(--ink)}
  .location svg{width:17px;height:24px}

  .wordmark{position:absolute;left:0;right:0;top:185px;display:flex;justify-content:center;align-items:center;gap:16px}
  .wordmark__dot{width:40px;height:40px;border-radius:50%;background:var(--pink)}
  .wordmark__name{font-family:"Lato",sans-serif;font-weight:400;font-size:50px;color:var(--purple);white-space:nowrap}

  .stripe{position:absolute;bottom:0;height:19px}
  .stripe--purple{left:0;width:240px;background:var(--purple)}
  .stripe--pink{left:249px;width:242px;background:var(--pink)}
  .stripe--teal{left:500px;width:243px;background:var(--teal)}
</style>
</head>
<body>
<main class="canvas">
  <section class="card card--front" aria-label="Card front">
    <div class="brand-tag"><span class="brand-dot"></span><span>Harborlight Elder Aides</span></div>

    <div class="identity">
      <h1 class="identity__name">Delia Parkhurst</h1>
      <p class="identity__role">Owner</p>
    </div>
    <div class="divider"></div>

    <ul class="contacts">
      <li class="contacts__phone">
        <svg viewBox="0 0 24 24" aria-hidden="true"><path fill="var(--pink)" d="M6.6 10.8a15.1 15.1 0 0 0 6.6 6.6l2.2-2.2a1 1 0 0 1 1-.25 11.4 11.4 0 0 0 3.6.57 1 1 0 0 1 1 1V20a1 1 0 0 1-1 1A17 17 0 0 1 3 4a1 1 0 0 1 1-1h3.5a1 1 0 0 1 1 1c0 1.25.2 2.46.57 3.6a1 1 0 0 1-.25 1z"/><path fill="none" stroke="var(--pink)" stroke-width="2" d="M14 3a7 7 0 0 1 7 7M14 7a3 3 0 0 1 3 3"/></svg>
        <span>936.482.5079</span>
      </li>
      <li>
        <svg viewBox="0 0 24 24" aria-hidden="true"><rect x="2" y="5" width="20" height="14" fill="var(--pink)"/><path d="M3 6l9 7 9-7" fill="none" stroke="#fff" stroke-width="1.6"/></svg>
        <span>Delia@harborlightelderaides.com</span>
      </li>
      <li>
        <svg viewBox="0 0 24 24" aria-hidden="true"><circle cx="12" cy="12" r="10" fill="var(--pink)"/><path d="M2.5 12h19M12 2c3 3 3 17 0 20M12 2c-3 3-3 17 0 20" fill="none" stroke="#fff" stroke-width="1.4"/></svg>
        <span>www.HarborlightElderAides.com</span>
      </li>
    </ul>

    <div class="location">
      <svg viewBox="0 0 24 34" aria-hidden="true"><path fill="var(--pink)" d="M12 0a12 12 0 0 0-12 12c0 9 12 22 12 22s12-13 12-22A12 12 0 0 0 12 0z"/><circle cx="12" cy="12" r="4.5" fill="#fff"/></svg>
      <span>Willowmere, Texas</span>
    </div>
  </section>

  <section class="card card--back" aria-label="Card back">
    <div class="wordmark">
      <span class="wordmark__dot"></span>
      <span class="wordmark__name">Harborlight Elder Aides</span>
    </div>
    <span class="stripe stripe--purple"></span>
    <span class="stripe stripe--pink"></span>
    <span class="stripe stripe--teal"></span>
  </section>
</main>
</body>
</html>
```